business card deign

Logo needs the following on it.
1. attached logo
2. Tagline - "If it keeps the ice frosty or the music loud...we handle it!"
3. Name- Dalton Pikes, Founder and CPO
4. Address - 412 E. Carver Avenue, Ste 2207, Tampa, FL. 33917
5. Phone - 555.318.4726

```html
<!DOCTYPE html>
<html lang="en">
<head>
<meta charset="utf-8">
<title>Kelvaro Business Card</title>
<link rel="stylesheet" href="https://fonts.googleapis.com/css2?family=Archivo+Narrow:wght@400;700&family=Arimo:wght@400&display=swap">
<style>
  :root {
    --page-bg: #d3d4d6;
    --card-light: #ffffff;
    --card-dark: #161616;
    --ink-dark: #111111;
    --ink-light: #ffffff;
    --ink-soft: #e6e6e6;
  }
  html, body {
    margin: 0;
    padding: 0;
    width: 900px;
    height: 1200px;
    overflow: hidden;
    background: var(--page-bg);
  }
  .canvas {
    position: relative;
    width: 900px;
    height: 1200px;
  }
  .card {
    position: absolute;
    left: 135px;
    width: 630px;
    height: 357px;
  }
  .card-front {
    top: 214px;
    background: var(--card-light);
    color: var(--ink-dark);
  }
  .card-back {
    top: 628px;
    background: var(--card-dark);
    color: var(--ink-light);
  }
  .brand-mark {
    position: absolute;
    border-radius: 50%;
  }
  .card-front .brand-mark {
    width: 78px;
    height: 78px;
    left: 276px;
    top: 130px;
    background: var(--ink-dark);
  }
  .card-back .brand-mark {
    width: 56px;
    height: 56px;
    left: 162px;
    top: 165px;
    background: var(--ink-light);
  }
  .brand-name {
    position: absolute;
    margin: 0;
    font-family: "Archivo Narrow", "Arial Narrow", sans-serif;
    font-weight: 700;
    letter-spacing: 0.42em;
    line-height: 1;
    text-align: center;
  }
  .card-front .brand-name {
    left: 0;
    width: 630px;
    top: 241px;
    font-size: 40px;
    padding-left: 0.42em;
    box-sizing: border-box;
  }
  .card-back .brand-name {
    left: 60px;
    width: 262px;
    top: 230px;
    font-size: 32px;
    padding-left: 0.42em;
    box-sizing: border-box;
  }
  .tagline {
    position: absolute;
    left: 0;
    width: 630px;
    top: 305px;
    margin: 0;
    text-align: center;
    font-family: "Archivo Narrow", "Arial Narrow", sans-serif;
    font-weight: 700;
    font-size: 16px;
    letter-spacing: 0.04em;
  }
  .divider {
    position: absolute;
    left: 314px;
    top: 97px;
    width: 2px;
    height: 164px;
    background: var(--ink-light);
  }
  .contact {
    position: absolute;
    left: 343px;
    top: 101px;
    font-family: "Arimo", Arial, sans-serif;
  }
  .contact-name {
    margin: 0;
    font-family: "Archivo Narrow", "Arial Narrow", sans-serif;
    font-weight: 700;
    font-size: 29px;
    line-height: 32px;
    letter-spacing: 0.01em;
  }
  .contact-title {
    margin: 4px 0 0;
    font-size: 14px;
    color: var(--ink-soft);
    letter-spacing: 0.02em;
  }
  .contact-phone {
    margin: 22px 0 0;
    font-size: 17px;
    letter-spacing: 0.05em;
    display: flex;
    align-items: center;
    gap: 6px;
  }
  .contact-phone svg { width: 12px; height: 12px; }
  .contact-address {
    margin: 14px 0 0;
    font-size: 14px;
    line-height: 26px;
    color: var(--ink-soft);
    font-style: normal;
    letter-spacing: 0.02em;
  }
</style>
</head>
<body>
<div class="canvas">
  <section class="card card-front">
    <span class="brand-mark" aria-hidden="true"></span>
    <h1 class="brand-name">KELVARO</h1>
    <p class="tagline">If it keeps the ice frosty or the music loud…we handle it!</p>
  </section>

  <section class="card card-back">
    <span class="brand-mark" aria-hidden="true"></span>
    <p class="brand-name">KELVARO</p>
    <span class="divider"></span>
    <div class="contact">
      <h2 class="contact-name">DALTON PIKES</h2>
      <p class="contact-title">Founder and CPO</p>
      <p class="contact-phone">
        <svg viewBox="0 0 24 24" aria-hidden="true"><path fill="#fff" d="M6.6 10.8a15.1 15.1 0 0 0 6.6 6.6l2.2-2.2c.3-.3.7-.4 1-.2 1.1.4 2.3.6 3.6.6.6 0 1 .4 1 1V20c0 .6-.4 1-1 1A17 17 0 0 1 3 4c0-.6.4-1 1-1h3.5c.6 0 1 .4 1 1 0 1.3.2 2.5.6 3.6.1.3 0 .7-.2 1z"/></svg>
        555.318.4726
      </p>
      <address class="contact-address">412 E. Carver Avenue, Ste 2207<br>Tampa, FL. 33917</address>
    </div>
  </section>
</div>
</body>
</html>
```